I need a label design to go on our jars of honey. Our company is called Marrowdale Honey Co. The type of honey is called Fernlight Glen Honey. The jars are 1kg. Attached is the label size. Left hand side needs to have nutritional info... as attached. Middle section is our company name, honey type, 1kg & Kauriwai, NZ. Right hand side needs to have info as per photo (raw honey etc). I would like to upload more pictures... but I’m unsure how to do this? Thanks, Carla

Target Market(s)

Honey consumers... families

Industry/Entity Type

Food Production

Colors

Designer to choose colors to be used in the design.

Requirements
Must have
• Nutritional info as per upload
• Type of honey & company name as per upload
• 1kg
• Address
Nice to have
• Similar fonts to upload.
• Possibly background image... floral or beach... very faint though.

```html
<!DOCTYPE html>
<html lang="en">
<head>
<meta charset="utf-8">
<title>Marrowdale Honey Co. – Fernlight Glen Honey label</title>
<link rel="stylesheet" href="https://fonts.googleapis.com/css2?family=Poiret+One&family=Kaushan+Script&family=Handlee&family=Arimo:wght@400;700&display=swap">
<style>
  :root {
    --rose: #b23a62;
    --rose-deep: #9b2c55;
    --ink: #8e2a50;
    --panel: #ffffff;
    --blush-1: #f6eef6;
    --blush-2: #eedcec;
    --blush-3: #f3d3e2;
    --lilac: #e4dcef;
  }
  * { box-sizing: border-box; margin: 0; padding: 0; }
  html, body { width: 1200px; height: 480px; overflow: hidden; background: #fff; }

  .label {
    position: relative;
    width: 1200px;
    height: 480px;
    overflow: hidden;
    font-family: "Arimo", Arial, sans-serif;
    color: var(--ink);
  }

  .label__backdrop {
    position: absolute;
    inset: 0;
    background:
      radial-gradient(ellipse 260px 200px at 1130px 110px, rgba(243,196,218,.85), transparent 70%),
      radial-gradient(ellipse 220px 160px at 860px 300px, rgba(240,190,214,.8), transparent 70%),
      radial-gradient(ellipse 200px 150px at 1080px 420px, rgba(238,200,222,.7), transparent 70%),
      radial-gradient(ellipse 240px 200px at 720px 220px, rgba(246,214,230,.6), transparent 70%),
      radial-gradient(ellipse 300px 240px at 500px 360px, rgba(230,220,240,.6), transparent 70%),
      linear-gradient(100deg, var(--blush-1) 0%, var(--lilac) 40%, var(--blush-2) 70%, var(--blush-3) 100%);
  }

  /* Left nutrition panel */
  .nutrition-panel {
    position: absolute;
    left: 0; top: 0;
    width: 366px; height: 480px;
    background: var(--panel);
    border-radius: 0 34px 34px 0;
  }
  .nutrition-panel__claim {
    position: absolute;
    left: 0; width: 366px; top: 43px;
    text-align: center;
    font-size: 14.5px;
    line-height: 18px;
  }
  .nutrition-table {
    position: absolute;
    left: 86px; top: 88px;
    width: 230px; height: 230px;
    border: 1px solid var(--ink);
    font-size: 10px;
    line-height: 12px;
  }
  .nutrition-table__head {
    padding: 7px 10px 0;
    height: 58px;
    border-bottom: 1px solid var(--ink);
  }
  .nutrition-table__cols {
    display: grid;
    grid-template-columns: 82px 64px 1fr;
    height: 46px;
    padding: 7px 10px 0;
    border-bottom: 1px solid var(--ink);
    font-size: 7.5px;
    line-height: 9px;
  }
  .nutrition-table__rows { padding: 12px 10px 0; }
  .nutrition-table__row {
    display: grid;
    grid-template-columns: 82px 64px 1fr;
    height: 15.8px;
    font-size: 10.5px;
  }
  .nutrition-panel__notes {
    position: absolute;
    left: 0; width: 366px; top: 331px;
    text-align: center;
    font-size: 10px;
    line-height: 11.8px;
  }
  .batch-info {
    position: absolute;
    left: 88px; top: 394px;
    font-size: 12px;
    font-weight: 700;
    line-height: 14.5px;
  }
  .batch-info__row { display: grid; grid-template-columns: 84px 10px; }

  /* Centre brand block */
  .brand {
    position: absolute;
    left: 416px; width: 396px; top: 0;
    height: 480px;
    text-align: center;
    color: var(--rose);
  }
  .brand__company {
    font-family: "Poiret One", "Helvetica Neue", sans-serif;
    font-weight: 400;
    font-size: 38px;
    letter-spacing: 5px;
    line-height: 56px;
    padding-top: 24px;
  }
  .brand__product {
    font-family: "Kaushan Script", cursive;
    font-weight: 400;
    font-size: 70px;
    line-height: 90px;
    margin-top: 38px;
  }
  .brand__weight {
    position: absolute;
    top: 398px; left: 0; width: 100%;
    font-family: "Poiret One", "Helvetica Neue", sans-serif;
    font-size: 18px;
    letter-spacing: 1px;
  }
  .brand__town {
    position: absolute;
    top: 430px; left: 0; width: 100%;
    font-family: "Poiret One", "Helvetica Neue", sans-serif;
    font-size: 18px;
    letter-spacing: 3px;
  }

  /* Right story block */
  .story {
    position: absolute;
    left: 864px; width: 300px; top: 31px;
    text-align: center;
    font-family: "Handlee", cursive;
    font-size: 16.5px;
    line-height: 25px;
    color: var(--rose-deep);
  }
  .story__origin { margin-bottom: 25px; }
  .story__raw { margin-bottom: 32px; }
  .story__signoff { margin-bottom: 29px; }
  .story__contact {
    position: absolute;
    left: 864px; width: 300px; top: 381px;
    text-align: center;
    font-family: "Handlee", cursive;
    font-style: normal;
    font-size: 11.5px;
    line-height: 14.6px;
    color: var(--rose-deep);
  }
</style>
</head>
<body>
<main class="label">
  <div class="label__backdrop" role="img" aria-label="Faint pink cherry blossom photograph fading across the label, densest on the right"></div>

  <section class="nutrition-panel">
    <p class="nutrition-panel__claim">100% New Zealand Honey<br>no added ingredients</p>

    <div class="nutrition-table">
      <div class="nutrition-table__head">
        NUTRITIONAL INFORMATION<br>
        Serving per package: 100<br>
        Serving size: 10g
      </div>
      <div class="nutrition-table__cols">
        <span></span>
        <span>Average<br>Quantity<br>per serving</span>
        <span>Average<br>Quantity<br>per 100g</span>
      </div>
      <div class="nutrition-table__rows">
        <div class="nutrition-table__row"><span>Energy</span><span>134kj</span><span>1340kj</span></div>
        <div class="nutrition-table__row"><span>Protein</span><span>0.04g</span><span>0.4g</span></div>
        <div class="nutrition-table__row"><span>Fat total</span><span>0g</span><span>0g</span></div>
        <div class="nutrition-table__row"><span>- saturated</span><span>0g</span><span>0g</span></div>
        <div class="nutrition-table__row"><span>Carbohydrate</span><span>7.9g</span><span>79.6g</span></div>
        <div class="nutrition-table__row"><span>-sugars</span><span>7.8g</span><span>78.1g</span></div>
        <div class="nutrition-table__row"><span>Sodium</span><span>1.2mg</span><span>12mg</span></div>
      </div>
    </div>

    <p class="nutrition-panel__notes">
      Store upright in a cool, dry place.<br>
      No refrigeration needed.<br>
      Not recommended for infants below<br>
      the age of 12 months
    </p>

    <div class="batch-info">
      <div class="batch-info__row"><span>Best Before</span><span>:</span></div>
      <div class="batch-info__row"><span>RMP</span><span>:</span></div>
      <div class="batch-info__row"><span>Batch No</span><span>:</span></div>
    </div>
  </section>

  <section class="brand">
    <h1 class="brand__company">MARROWDALE<br>HONEY CO.</h1>
    <h2 class="brand__product">Fernlight<br>Glen Honey</h2>
    <p class="brand__weight">1kg</p>
    <p class="brand__town">KAURIWAI, NZ</p>
  </section>

  <section class="story">
    <p class="story__origin">Sourced from the beautiful<br>Kauriwai Peninsula</p>
    <p class="story__raw">Our honey comes to you raw &amp;<br>unpasturized, ensuring it retains<br>all the natural goodness!</p>
    <p class="story__signoff">Arohanui<br>Rowan, Carla &amp; boys</p>
    <p class="story__thanks">‘Marrowdale’ – all thanks to God for his<br>incredible creation!</p>
  </section>

  <address class="story__contact">
    www.marrowdalehoney.co.nz<br>
    24 Kowhai Lane<br>
    Kauriwai<br>
    New Zealand
  </address>
</main>
</body>
</html>
```